MintVela business cards

We want to create two sets of cards. One general card for mintvela [staff] and one card for the founder of the company. Below is the general/basic information for you to format/display on side of the cards:
--Company address: 418 Larkmoor Street, New York, NY 10087
--Main phone: 212-736-5182
Will also provide you with secondary 1-800 number
--company website: www.mintvela.example
--email address for general card: frontdesk@mintvela.example
--email address (for dr hollings's card: md@mintvela.example
--titles for dr hollings's card: Founder, Medical Director
--Dr. Hollings's name on the card should read: Gregor T. Hollings, MD
You can also play around with mintvela's tag line: Quiet Glow Keeps Its Promise (TM or R should be attached as a trademark has been filed)
Reason: More time to design something awesome. This company is an aesthetic medical company that offers cool and safe cosmetic treatments
For the business card design for the doctor, please change the doctor's name to look like this above his title: Gregor T. Hollings, MD instead of using Dr. Gregor....etc
Reason: WILL NOT BE ABLE TO VIEW AND FINALIZE DESIGNS UNTIL I RETURN FROM MEDICAL CONFERENCE, WHICH WILL BE ON SUNDAY/MONDAY. MY APOLOGIES
can everyone try making it very minimalistic
A Bit of a change...
Can everyone take a stab at using a grey "raw" or eco friendly stock paper. We are interested to see the designs you come up with.
Business

```html
<!DOCTYPE html>
<html lang="en">
<head>
<meta charset="utf-8">
<title>MintVela Business Cards</title>
<link rel="stylesheet" href="https://fonts.googleapis.com/css2?family=Saira:wght@300;400;500&display=swap">
<style>
  :root {
    --stage: #e6e7e9;
    --card-dark: #222224;
    --card-shadow: rgba(0, 0, 0, 0.25);
    --brand-blue: #4b92d8;
    --blue-deep: #2f6fbf;
    --blue-light: #4aa3e0;
    --stripe-grey: #7d7f84;
    --text-light: #f2f4f7;
    --text-muted: #c9ccd2;
  }
  * { box-sizing: border-box; margin: 0; padding: 0; }
  html, body { width: 1200px; height: 900px; overflow: hidden; }
  body {
    background: var(--stage);
    font-family: "Saira", sans-serif;
    display: flex;
    align-items: center;
    justify-content: center;
    gap: 40px;
  }
  .card {
    position: relative;
    width: 540px;
    height: 330px;
    border-radius: 30px;
    background: var(--card-dark);
    overflow: hidden;
    box-shadow: 0 14px 30px var(--card-shadow);
    color: var(--text-light);
  }
  .card__wave { position: absolute; inset: 0; width: 100%; height: 100%; }
  .brand-name {
    font-family: "Saira", sans-serif;
    font-weight: 300;
    color: var(--brand-blue);
    line-height: 1;
    letter-spacing: -0.5px;
  }
  .card--front .brand-name {
    position: absolute;
    left: 26px;
    top: 18px;
    font-size: 66px;
  }
  .person {
    position: absolute;
    left: 42px;
    top: 96px;
    text-transform: uppercase;
    line-height: 1.3;
  }
  .person__name { font-size: 16px; font-weight: 400; letter-spacing: 1.5px; }
  .person__title { font-size: 11px; font-weight: 300; letter-spacing: 1.4px; color: var(--text-muted); }
  .address {
    position: absolute;
    left: 30px;
    top: 180px;
    font-size: 13px;
    font-weight: 300;
    line-height: 1.5;
    font-style: normal;
  }
  .contacts {
    position: absolute;
    right: 24px;
    bottom: 18px;
    list-style: none;
    font-size: 11.5px;
    font-weight: 300;
    letter-spacing: 0.6px;
  }
  .contacts li {
    display: flex;
    align-items: center;
    justify-content: flex-end;
    gap: 8px;
    height: 19px;
  }
  .contacts svg { width: 11px; height: 11px; fill: none; stroke: var(--text-light); stroke-width: 1.6; }
  .card--back {
    display: flex;
    flex-direction: column;
    align-items: center;
    justify-content: center;
    gap: 14px;
  }
  .card--back .brand-name { font-size: 100px; }
  .tagline {
    font-size: 13px;
    font-weight: 300;
    letter-spacing: 2px;
    text-transform: uppercase;
    color: var(--text-muted);
  }
</style>
</head>
<body>
  <article class="card card--front">
    <svg class="card__wave" viewBox="0 0 540 330" preserveAspectRatio="none" aria-hidden="true">
      <defs>
        <radialGradient id="bandBlue" cx="0.6" cy="0.45" r="0.8">
          <stop offset="0" stop-color="var(--blue-light)"/>
          <stop offset="1" stop-color="var(--blue-deep)"/>
        </radialGradient>
      </defs>
      <path d="M0,148 C170,142 330,214 540,196 L540,330 L0,330 Z" fill="var(--stripe-grey)"/>
      <path d="M0,157 C170,151 330,223 540,205 L540,330 L0,330 Z" fill="url(#bandBlue)"/>
    </svg>
    <div class="brand-name">mintvela</div>
    <div class="person">
      <div class="person__name">Gregor T. Hollings, MD</div>
      <div class="person__title">Founder, Medical Director</div>
    </div>
    <address class="address">418 Larkmoor Street,<br>New York, NY 10087</address>
    <ul class="contacts">
      <li>212-736-5182
        <svg viewBox="0 0 12 12"><path d="M3 1 L5 3.5 L4 5 Q5.5 7.5 7 8 L8.5 7 L11 9 L9.5 11 Q3 10 1 2.5 Z"/></svg></li>
      <li>1-800-555-0172
        <svg viewBox="0 0 12 12"><rect x="3" y="0.8" width="6" height="10.4" rx="1"/><path d="M5 9.5 H7"/></svg></li>
      <li>212-736-5183
        <svg viewBox="0 0 12 12"><rect x="1" y="4" width="10" height="7"/><path d="M3 4 V1 H9 V4 M3 7 H9"/></svg></li>
      <li>md@mintvela.example
        <svg viewBox="0 0 12 12"><rect x="1" y="2.5" width="10" height="7"/><path d="M1 2.5 L6 6.5 L11 2.5"/></svg></li>
      <li>www.mintvela.example
        <svg viewBox="0 0 12 12"><circle cx="6" cy="6" r="5"/><ellipse cx="6" cy="6" rx="2.2" ry="5"/><path d="M1 6 H11"/></svg></li>
    </ul>
  </article>

  <article class="card card--back">
    <div class="brand-name">mintvela</div>
    <p class="tagline">Quiet Glow Keeps Its Promise&trade;</p>
  </article>
</body>
</html>
```